Design a business card
Business name: Harbourline Growth Advisory
Improving Business Profitibility

- An Overview of the Business & Service:

Business Performance Consulting

- The Target Market: Small to medium-sized business

- Design Specifics:
White card, blue ink, moon eclipse

No Logo

Target Market(s)

Small to medium-sized business

Font styles to use
Sans Serif

```html
<!DOCTYPE html>
<html lang="en">
<head>
<meta charset="utf-8">
<title>Harbourline Growth Advisory — Business Card</title>
<link href="https://fonts.googleapis.com/css2?family=Oswald:wght@500&family=Open+Sans:wght@400;600&display=swap" rel="stylesheet">
<style>
  :root {
    --backdrop: #161616;
    --card: #1f2022;
    --card-edge: #2a2b2e;
    --blue: #1f5bb5;
    --text-light: #e6e6e6;
    --text-muted: #b5b5b5;
    --rule: #3a3b3f;
    --ghost: rgba(255, 255, 255, 0.035);
  }
  * { box-sizing: border-box; margin: 0; padding: 0; }
  html, body {
    width: 1200px; height: 900px; overflow: hidden;
    background: var(--backdrop);
    font-family: "Open Sans", Arial, sans-serif;
  }
  .stage {
    width: 1200px; height: 900px;
    display: flex; flex-direction: column;
    align-items: center; justify-content: center; gap: 40px;
  }
  .card {
    position: relative;
    width: 560px; height: 320px;
    background: var(--card);
    border: 1px solid var(--card-edge);
    border-radius: 26px;
    overflow: hidden;
    box-shadow: 0 16px 40px rgba(0, 0, 0, 0.55);
  }
  .ghost-disc {
    position: absolute;
    width: 300px; height: 300px; border-radius: 50%;
    border: 34px solid var(--ghost);
    left: -90px; top: 20px;
  }
  .brand-dot {
    width: 86px; height: 86px; border-radius: 50%;
    border: 12px solid var(--blue);
  }
  .brand-name {
    font-family: "Oswald", "Arial Narrow", sans-serif;
    font-weight: 500;
    color: var(--blue);
    text-transform: uppercase;
    letter-spacing: 0.5px;
    white-space: nowrap;
  }

  /* Front */
  .card-front .brand {
    position: absolute; left: 0; right: 0; top: 62px;
    display: flex; flex-direction: column; align-items: center; gap: 18px;
  }
  .card-front .brand-name { font-size: 26px; line-height: 1; }
  .tagline {
    position: absolute; left: 0; right: 0; bottom: 52px;
    text-align: center;
    font-family: "Oswald", "Arial Narrow", sans-serif;
    font-weight: 500; font-size: 15px; letter-spacing: 1.4px;
    color: var(--text-muted); text-transform: uppercase;
  }

  /* Back */
  .card-back .brand {
    position: absolute; right: 40px; top: 26px;
    display: flex; flex-direction: column; align-items: center; gap: 10px;
  }
  .card-back .brand .brand-dot { width: 58px; height: 58px; border-width: 9px; }
  .card-back .brand-name { font-size: 20px; line-height: 1; }
  .address {
    position: absolute; right: 40px; top: 128px;
    padding-top: 12px; width: 250px;
    border-top: 1px solid var(--rule);
    text-align: right; color: var(--text-light);
    font-size: 15px; line-height: 1.45;
  }
  .person {
    position: absolute; left: 36px; bottom: 28px; width: 215px;
  }
  .person-name {
    font-family: "Oswald", "Arial Narrow", sans-serif;
    font-weight: 500; font-size: 21px; color: var(--blue);
    text-transform: uppercase; letter-spacing: 0.3px; line-height: 1.1;
    white-space: nowrap;
  }
  .person-role {
    color: var(--text-light); font-size: 15px;
    padding-bottom: 8px; margin-bottom: 8px;
    border-bottom: 1px solid var(--rule);
  }
  .contact-list { list-style: none; }
  .contact-list li {
    display: flex; align-items: center; gap: 9px;
    color: var(--text-light); font-size: 14.5px; line-height: 1.55;
    white-space: nowrap;
  }
  .contact-list svg { width: 13px; height: 13px; fill: var(--blue); flex: none; }
</style>
</head>
<body>
<main class="stage">

  <section class="card card-front" aria-label="Card front">
    <div class="ghost-disc"></div>
    <div class="brand">
      <div class="brand-dot"></div>
      <div class="brand-name">Harbourline Growth Advisory</div>
    </div>
    <p class="tagline">Improving Business Profitibility</p>
  </section>

  <section class="card card-back" aria-label="Card back">
    <div class="ghost-disc"></div>
    <div class="brand">
      <div class="brand-dot"></div>
      <div class="brand-name">Harbourline Growth Advisory</div>
    </div>
    <p class="address">48 Quayside Row<br>Portmarrow, 204180</p>

    <div class="person">
      <h1 class="person-name">Desmond R Akerly</h1>
      <p class="person-role">Managing Director</p>
      <ul class="contact-list">
        <li>
          <svg viewBox="0 0 16 16" aria-hidden="true"><path d="M1 5c0-2 3-3 7-3s7 1 7 3v1.5h-3.5V5h-7v1.5H1zM3 8h10l1.5 6h-13z"/></svg>
          044-555 010 247
        </li>
        <li>
          <svg viewBox="0 0 16 16" aria-hidden="true"><path d="M4 0h8a1 1 0 0 1 1 1v14a1 1 0 0 1-1 1H4a1 1 0 0 1-1-1V1a1 1 0 0 1 1-1zm1 2v10h6V2zm3 11a1 1 0 1 0 0 2 1 1 0 0 0 0-2z"/></svg>
          044-555 010 248
        </li>
        <li>
          <svg viewBox="0 0 16 16" aria-hidden="true"><path d="M0 3h16v1.2L8 9 0 4.2zm0 2.6 8 4.8 8-4.8V13H0z"/></svg>
          info@harbourlinegrowth.com
        </li>
        <li>
          <svg viewBox="0 0 16 16" aria-hidden="true"><circle cx="8" cy="8" r="7.5"/></svg>
          www.harbourlinegrowth.com
        </li>
      </ul>
    </div>
  </section>

</main>
</body>
</html>
```